Moderne Visitenkarten für Medizintechnikfirma
Zielgruppe
Vertriebsfirma von moderner und innovativer Medizintechnik
Zielgruppe: Ärzte, Kliniken, Medizintechnikfirmen, Patienten
Aufgabenstellung
Besonderes, modernes, auffälliges und ansprechendes Design ohne überladen oder aufdringlich zu sein
Farbenorientierung kann am Logo und der Website geschehen. Wenn zum Logo harmonierend, sind aber auch andere Farben gerne gesehen.
Format: eher horizontal, vertikal aber auch möglich, abgerundete Ecken einplanen
Wenn möglich folgende Infos bitte schon auf die Karten bringen (pro Person eine Karte):
Konrad Faltermann (CEO)
konrad.faltermann@vitalis-partner.de
(Vitalis Partner GmbH
Lindenhof 12
26210 Grünstedt)
www.vitalis-partner.de
info@vitalis-partner.de
Jonas Prasken (CoS)
jonas.prasken@vitalis-partner.de
Die allgemeinen Firmeninfos können deutlich kleiner sein. Anschrift nur wenn es dadurch nicht zu viel werden würde.

```html
<!DOCTYPE html>
<html lang="de">
<head>
<meta charset="utf-8">
<title>Vitalis Partner – Visitenkarten</title>
<link rel="stylesheet" href="https://fonts.googleapis.com/css2?family=Montserrat:wght@500;600;700&display=swap">
<style>
  :root {
    --purple: #46347f;
    --orange: #e8432a;
    --paper: #ffffff;
    --backdrop: #e8eaee;
    --shadow: rgba(40, 40, 70, 0.16);
  }
  * { box-sizing: border-box; margin: 0; padding: 0; }
  html, body { width: 1200px; height: 900px; overflow: hidden; }
  body {
    background: var(--backdrop);
    font-family: "Montserrat", Arial, sans-serif;
    display: flex;
    flex-direction: column;
    align-items: center;
    justify-content: center;
    gap: 40px;
  }
  .card {
    position: relative;
    width: 640px;
    height: 388px;
    background: var(--paper);
    border-radius: 18px;
    overflow: hidden;
    box-shadow: 0 10px 28px var(--shadow);
  }
  .brand {
    position: absolute;
    top: 64px;
    left: 210px;
    display: flex;
    align-items: center;
    gap: 14px;
  }
  .brand-dot {
    width: 26px; height: 26px;
    border-radius: 50%;
    background: var(--purple);
  }
  .brand-name {
    font-size: 42px;
    font-weight: 700;
    color: var(--purple);
    letter-spacing: -0.5px;
  }
  .person {
    position: absolute;
    left: 40px;
    top: 190px;
  }
  .person-name {
    font-size: 27px;
    font-weight: 700;
    color: var(--orange);
    margin-bottom: 12px;
  }
  .person-role { color: var(--purple); font-weight: 600; }
  .line {
    display: flex;
    align-items: center;
    gap: 9px;
    font-size: 14px;
    font-weight: 600;
    margin-bottom: 7px;
  }
  .line--purple { color: var(--purple); }
  .line--orange { color: var(--orange); }
  .icon {
    width: 19px; height: 19px;
    border-radius: 50%;
    flex: none;
    display: flex; align-items: center; justify-content: center;
  }
  .icon svg { width: 11px; height: 11px; fill: #fff; }
  .icon--purple { background: var(--purple); }
  .icon--orange { background: var(--orange); }
  .company {
    position: absolute;
    left: 400px;
    top: 172px;
  }
  .company .line { font-size: 12.5px; margin-bottom: 8px; align-items: flex-start; }
  .address { line-height: 1.35; }
  .band-orange {
    position: absolute;
    left: 0; bottom: 0;
    width: 380px; height: 20px;
    background: var(--orange);
  }
  .band-purple {
    position: absolute;
    right: 0; bottom: 0;
    width: 286px; height: 48px;
    background: var(--purple);
    border-top-left-radius: 40px;
    display: flex; align-items: center; justify-content: center;
    color: #fff;
    font-size: 14px;
    font-weight: 600;
    letter-spacing: 0.3px;
  }
</style>
</head>
<body>
<svg width="0" height="0" style="position:absolute">
  <defs>
    <symbol id="i-phone" viewBox="0 0 24 24"><path d="M6.6 10.8a15.1 15.1 0 0 0 6.6 6.6l2.2-2.2a1 1 0 0 1 1-.25 11.4 11.4 0 0 0 3.6.57 1 1 0 0 1 1 1V20a1 1 0 0 1-1 1A17 17 0 0 1 3 4a1 1 0 0 1 1-1h3.5a1 1 0 0 1 1 1c0 1.25.2 2.45.57 3.57a1 1 0 0 1-.25 1z"/></symbol>
    <symbol id="i-mail" viewBox="0 0 24 24"><path d="M3 5h18v14H3zm2 2v.5l7 4.5 7-4.5V7zm0 3v7h14v-7l-7 4.5z"/></symbol>
    <symbol id="i-pin" viewBox="0 0 24 24"><path d="M12 2a7 7 0 0 0-7 7c0 5 7 13 7 13s7-8 7-13a7 7 0 0 0-7-7zm0 9.5A2.5 2.5 0 1 1 12 6.5a2.5 2.5 0 0 1 0 5z"/></symbol>
  </defs>
</svg>

<article class="card card--ceo">
  <div class="brand"><span class="brand-dot"></span><span class="brand-name">Vitalis Partner</span></div>
  <div class="person">
    <p class="person-name">Konrad Faltermann <span class="person-role">(CEO)</span></p>
    <p class="line line--purple"><span class="icon icon--purple"><svg><use href="#i-phone"/></svg></span>+4916090412273</p>
    <p class="line line--orange"><span class="icon icon--orange"><svg><use href="#i-mail"/></svg></span>konrad.faltermann@vitalis-partner.de</p>
  </div>
  <div class="company">
    <p class="line line--purple"><span class="icon icon--purple"><svg><use href="#i-pin"/></svg></span><span class="address">(Vitalis Partner GmbH<br>Lindenhof 12<br>26210 Grünstedt)</span></p>
    <p class="line line--orange"><span class="icon icon--orange"><svg><use href="#i-mail"/></svg></span>info@vitalis-partner.de</p>
    <p class="line line--purple"><span class="icon icon--purple"><svg><use href="#i-phone"/></svg></span>0800-5551230</p>
  </div>
  <div class="band-orange"></div>
  <div class="band-purple">www.vitalis-partner.de</div>
</article>

<article class="card card--cos">
  <div class="brand"><span class="brand-dot"></span><span class="brand-name">Vitalis Partner</span></div>
  <div class="person">
    <p class="person-name">Jonas Prasken <span class="person-role">(CoS)</span></p>
    <p class="line line--purple"><span class="icon icon--purple"><svg><use href="#i-phone"/></svg></span>+4915288406172</p>
    <p class="line line--orange"><span class="icon icon--orange"><svg><use href="#i-mail"/></svg></span>jonas.prasken@vitalis-partner.de</p>
  </div>
  <div class="company">
    <p class="line line--purple"><span class="icon icon--purple"><svg><use href="#i-pin"/></svg></span><span class="address">(Vitalis Partner GmbH<br>Lindenhof 12<br>26210 Grünstedt)</span></p>
    <p class="line line--orange"><span class="icon icon--orange"><svg><use href="#i-mail"/></svg></span>info@vitalis-partner.de</p>
    <p class="line line--purple"><span class="icon icon--purple"><svg><use href="#i-phone"/></svg></span>0800-5551230</p>
  </div>
  <div class="band-orange"></div>
  <div class="band-purple">www.vitalis-partner.de</div>
</article>
</body>
</html>
```